In need of an AWESOME website for our Water Re-filling Store

The project is to design a website for our retail store front with the website www.quellbrookfillhouse.com. Currently if you go to that site it redirects you to our other site www.quellbrookbottleworks.com which is just our water bottle website. So, I need a new website created for www.quellbrookfillhouse.com (retail storefront)
Use our Squarespace to create a site with pages to help educate, tell about us, link to our water bottle brand site that is already created with Squarespace, and show the family and community aspects that we believe in. Our current water bottle website is www.quellbrookbottleworks.com for reference
We also sell hydration products, especially PRZQ products and have access to digital media through our PRZQ dealer site. we sell bottles, dispensers and other supplies for water refilling customers. We sell Ice as well.

Target Market(s)

Local residents looking to fill up their 1-5 gallon water jugs

Industry/Entity Type

Alkaline and Purified Water Retail Re-filling Store

Coding

Coded - Design and coding required

Font styles to use
Serif
Sans Serif

Colors
0054AA
0677BA
7BADD7
CADEEF
E8F1F8

Requirements
Must have
• pictures of our family in the about us section and pictures of our store inside and out.

```html
<!DOCTYPE html>
<html lang="en">
<head>
<meta charset="utf-8">
<title>Quellbrook Fill House</title>
<link href="https://fonts.googleapis.com/css2?family=Roboto:wght@400;500;700&family=Lato:wght@400;700&display=swap" rel="stylesheet">
<style>
:root{
  --navy:#2a2461;
  --blue:#0054aa;
  --blue-mid:#0677ba;
  --blue-soft:#7badd7;
  --blue-pale:#cadeef;
  --blue-mist:#e8f1f8;
  --ink:#111;
  --grey-text:#555;
  --panel:#f1f1f1;
  --white:#fff;
}
*{margin:0;padding:0;box-sizing:border-box}
html,body{width:1200px;height:2996px;overflow:hidden;background:var(--white)}
body{position:relative;font-family:'Lato',sans-serif;color:var(--ink)}
a{color:inherit;text-decoration:none}
.abs{position:absolute}

/* header */
.site-header{position:absolute;left:0;top:0;width:1200px;height:79px;background:var(--white);z-index:3}
.brand-badge{position:absolute;left:100px;top:-40px;width:226px;height:160px;border-radius:50%;background:var(--white);z-index:4;display:flex;align-items:flex-end;justify-content:center;padding-bottom:36px}
.brand-name{font-family:'Roboto',sans-serif;font-weight:500;font-size:21px;color:var(--blue);text-align:center;line-height:1.15}
.nav{position:absolute;top:24px;left:0;width:1200px;height:34px;font-family:'Roboto',sans-serif;font-size:15px}
.nav a{position:absolute;top:0;line-height:34px;color:#222}
.nav .is-active{left:393px;width:76px;background:var(--blue);color:var(--white);border-radius:17px;text-align:center;font-weight:500}
.btn-contact{position:absolute;left:975px;top:21px;width:112px;height:42px;border-radius:21px;background:var(--navy);color:var(--white);font-family:'Roboto',sans-serif;font-weight:700;font-size:15px;line-height:42px;text-align:center}

/* hero */
.hero-copy{position:absolute;left:0;top:79px;width:643px;height:581px;background:radial-gradient(ellipse at 60% 55%,#2f7fe0 0%,var(--blue) 55%,#00449a 100%)}
.hero-photo{position:absolute;left:643px;top:79px;width:557px;height:581px;background:linear-gradient(180deg,#a9977b 0%,#8c7c62 55%,#2a2a2a 78%,#1c1c1c 100%)}
.hero-title{position:absolute;left:107px;top:215px;font-family:'Roboto',sans-serif;font-weight:700;font-size:63px;line-height:75px;color:var(--white)}
.hero-text{position:absolute;left:111px;top:382px;width:440px;font-family:'Roboto',sans-serif;font-weight:500;font-size:18.5px;line-height:29px;color:var(--white)}
.pill{position:absolute;height:42px;border-radius:21px;font-family:'Roboto',sans-serif;font-weight:700;font-size:14.5px;line-height:42px;text-align:center}
.pill-dark{background:var(--navy);color:var(--white)}
.pill-light{background:var(--white);color:var(--ink)}

/* section titles */
.section-title{position:absolute;left:0;width:1200px;text-align:center;font-family:'Roboto',sans-serif;font-weight:500;font-size:42px;color:var(--ink)}
.section-title span{color:var(--blue);font-weight:700}
.swoosh{position:absolute}

/* offers */
.offer-card{position:absolute;top:860px;width:312px;height:368px;background:var(--white);border-radius:6px;box-shadow:0 3px 14px rgba(0,0,0,.12)}
.offer-card.is-featured{border:2px solid var(--blue-soft)}
.offer-media{position:absolute;left:13px;top:15px;width:291px;height:288px;border-radius:4px}
.offer-label{position:absolute;left:0;top:322px;width:100%;text-align:center;font-family:'Roboto',sans-serif;font-weight:500;font-size:24px}
.is-featured .offer-label{color:var(--blue-mid)}
.arrow{position:absolute;top:1038px;width:28px;height:28px;border-radius:50%}

/* about */
.about-photo{position:absolute;left:0;top:1328px;width:599px;height:515px;background:linear-gradient(180deg,#b5ab9a 0%,#8f8779 45%,#7b7468 100%)}
.about-panel{position:absolute;left:599px;top:1328px;width:601px;height:515px;background:var(--panel)}
.about-title{position:absolute;left:643px;top:1364px;font-family:'Roboto',sans-serif;font-weight:500;font-size:42px}
.about-title span{color:var(--blue);font-weight:700}
.about-sub{position:absolute;left:643px;top:1456px;font-family:'Roboto',sans-serif;font-weight:700;font-size:24px;color:var(--blue-mid)}
.about-text{position:absolute;left:644px;width:449px;font-size:15px;line-height:30px;color:var(--grey-text);text-align:justify}

/* gallery */
.tile{position:absolute;border-radius:4px}
.tile-caption{position:absolute;left:141px;top:2403px;font-family:'Roboto',sans-serif;font-weight:500;font-size:24px;color:var(--white)}

/* footer */
.site-footer{position:absolute;left:0;top:2615px;width:1200px;height:381px;background:radial-gradient(ellipse at 50% 40%,#1f6fd0 0%,var(--blue) 60%,#004a9c 100%);color:var(--white)}
.footer-brand{position:absolute;left:109px;top:82px;width:226px;text-align:center;font-family:'Roboto',sans-serif;font-weight:500;font-size:30px;line-height:38px}
.footer-brand small{display:block;font-size:18px;letter-spacing:4px;border-top:2px solid var(--white);margin-top:6px;padding-top:4px}
.social{position:absolute;top:238px;width:34px;height:34px;border-radius:50%;background:var(--white)}
.social.is-first{background:var(--blue-mid);border:2px solid var(--white)}
.footer-heading{position:absolute;top:90px;font-family:'Lato',sans-serif;font-weight:700;font-size:22px}
.footer-links{position:absolute;top:124px;list-style:none;font-size:15.5px;font-weight:700;line-height:33.7px}
.contact-item{position:absolute;left:908px;font-size:15px;line-height:20px}
.contact-icon{position:absolute;left:871px}
.footer-rule{position:absolute;left:112px;top:335px;width:976px;height:2px;background:var(--white)}
.copyright{position:absolute;left:0;top:350px;width:1200px;text-align:center;font-size:12.5px}
</style>
</head>
<body>

<header class="site-header">
  <nav class="nav">
    <a class="is-active" href="#">Home</a>
    <a style="left:494px" href="#">About Us</a>
    <a style="left:597px" href="#">Products</a>
    <a style="left:705px" href="#">Hydration Education</a>
    <a style="left:884px" href="#">Gallery</a>
  </nav>
  <a class="btn-contact" href="#">Contact Us</a>
</header>
<div class="brand-badge"><div class="brand-name">Quellbrook<br>Fill House</div></div>

<section>
  <div class="hero-copy" role="img" aria-label="Rippling blue water surface"></div>
  <div class="hero-photo" role="img" aria-label="Storefront exterior with the shop sign above glass doors"></div>
  <h1 class="hero-title">Hydration<br>Starts Here</h1>
  <p class="hero-text">Your local family-owned hydration destination for water refills, ice, bottles, dispensers, and premium electrolyte products.</p>
  <a class="pill pill-dark" style="left:112px;top:488px;width:147px" href="#">Visit Our Store</a>
  <a class="pill pill-light" style="left:274px;top:488px;width:182px" href="#">Shop Water Bottles</a>
</section>

<section>
  <h2 class="section-title" style="top:743px">What <span>We Offer</span></h2>
  <svg class="swoosh" style="left:548px;top:795px" width="104" height="18" viewBox="0 0 104 18"><path d="M2 14 C30 2 70 2 102 10" fill="none" stroke="var(--navy)" stroke-width="2.5" stroke-linecap="round"/></svg>

  <svg class="arrow" style="left:32px" viewBox="0 0 28 28"><circle cx="14" cy="14" r="14" fill="var(--navy)"/><path d="M16 8 L10 14 L16 20" fill="none" stroke="#fff" stroke-width="2.5"/></svg>
  <svg class="arrow" style="left:1129px" viewBox="0 0 28 28"><circle cx="14" cy="14" r="13" fill="#e2e2e2"/><path d="M12 8 L18 14 L12 20" fill="none" stroke="#fff" stroke-width="2.5"/></svg>

  <article class="offer-card" style="left:112px">
    <div class="offer-media" role="img" aria-label="Ice freezer stocked with bagged ice" style="background:linear-gradient(180deg,#7fb0de 0%,#2c3035 18%,#cfd6de 60%,#b9c2cc 100%)"></div>
    <h3 class="offer-label">Ice Sales</h3>
  </article>
  <article class="offer-card is-featured" style="left:443px">
    <div class="offer-media" role="img" aria-label="Three five-gallon water jugs with splashing water" style="background:radial-gradient(ellipse at 50% 55%,#5f9fd6 0%,#a9cdec 45%,#fff 75%)"></div>
    <h3 class="offer-label">Water Refills</h3>
  </article>
  <article class="offer-card" style="left:772px">
    <div class="offer-media" role="img" aria-label="Cooler shelves stocked with PRZQ hydration drink cans" style="background:linear-gradient(180deg,#2d2d2d 0%,#8e8d8e 40%,#6b5a5c 70%,#3a3334 100%)"></div>
    <h3 class="offer-label">PRZQ Hydration Drinks</h3>
  </article>
</section>

<section>
  <div class="about-photo" role="img" aria-label="The owners' family standing together in shallow water at the beach"></div>
  <div class="about-panel"></div>
  <h2 class="about-title">About <span>Us</span></h2>
  <svg class="swoosh" style="left:641px;top:1418px" width="104" height="18" viewBox="0 0 104 18"><path d="M2 14 C30 2 70 2 102 10" fill="none" stroke="var(--navy)" stroke-width="2.5" stroke-linecap="round"/></svg>
  <h3 class="about-sub">Family Owned. Community Focused.</h3>
  <p class="about-text" style="top:1498px">At Quellbrook Fill House, we believe clean hydration should be simple, affordable, and accessible for everyone. As a proud family-owned business, we created our store to serve our community with high-quality water refill options, premium hydration products, ice, reusable bottles, dispensers, and friendly service you can count on.</p>
  <p class="about-text" style="top:1657px">What started as a passion for healthier living and helping others has grown into a local destination where families, athletes, workers, and everyday customers .</p>
  <a class="pill pill-dark" style="left:643px;top:1763px;width:113px" href="#">Read More</a>
</section>

<section>
  <h2 class="section-title" style="top:1930px">Our <span>Gallery</span></h2>
  <svg class="swoosh" style="left:548px;top:1982px" width="104" height="18" viewBox="0 0 104 18"><path d="M2 14 C30 2 70 2 102 10" fill="none" stroke="var(--navy)" stroke-width="2.5" stroke-linecap="round"/></svg>

  <div class="tile" style="left:112px;top:2037px;width:444px;height:417px;background:linear-gradient(160deg,#3f5fae 0%,#3b3f55 45%,#6e6a70 100%)" role="img" aria-label="Staff member posing with a holiday costume character in the shop"></div>
  <span class="tile-caption">Lorm Ipsum Dolor Siet</span>
  <div class="tile" style="left:579px;top:2037px;width:219px;height:203px;background:linear-gradient(180deg,#c9c1b4 0%,#8d8478 55%,#e4e2df 100%)" role="img" aria-label="Owners standing behind rows of water bottles"></div>
  <div class="tile" style="left:811px;top:2037px;width:278px;height:203px;background:linear-gradient(180deg,#e7e8ea 0%,#2a5bc0 45%,#7a7d83 100%)" role="img" aria-label="Store interior with blue walls and refill stations"></div>
  <div class="tile" style="left:579px;top:2251px;width:279px;height:203px;background:linear-gradient(90deg,#8b5a2b 0%,#6b2f3a 50%,#c9b32c 100%)" role="img" aria-label="Row of bottled juices on the counter"></div>
  <div class="tile" style="left:871px;top:2251px;width:218px;height:203px;background:linear-gradient(180deg,#2b5fc4 0%,#2459b8 55%,#55607a 100%)" role="img" aria-label="Two staff members by the refill equipment"></div>
  <a class="pill pill-dark" style="left:544px;top:2485px;width:113px" href="#">View All</a>
</section>

<footer class="site-footer">
  <div class="footer-brand">Quellbrook<small>FILL HOUSE</small></div>
  <a class="social is-first" style="left:143px" href="#" aria-label="Social profile 1"></a>
  <a class="social" style="left:185px" href="#" aria-label="Social profile 2"></a>
  <a class="social" style="left:231px" href="#" aria-label="Social profile 3"></a>
  <a class="social" style="left:277px" href="#" aria-label="Social profile 4"></a>

  <h4 class="footer-heading" style="left:465px">Quick Links</h4>
  <ul class="footer-links" style="left:469px">
    <li>Home</li><li>About Us</li><li>Products</li><li>Hydration Education</li><li>Gallery</li><li>Contact Us</li>
  </ul>
  <h4 class="footer-heading" style="left:662px">Other Links</h4>
  <ul class="footer-links" style="left:666px">
    <li>Privacy &nbsp;Policy</li><li>Terms &amp; Conditions</li><li>Disclaimer</li><li>Support</li><li>Help</li><li>FAQ's</li>
  </ul>
  <h4 class="footer-heading" style="left:871px;top:93px">Contact Info</h4>

  <svg class="contact-icon" style="top:132px" width="22" height="22" viewBox="0 0 22 22"><circle cx="11" cy="11" r="11" fill="#fff"/><path d="M11 4a5 5 0 0 0-5 5c0 4 5 9 5 9s5-5 5-9a5 5 0 0 0-5-5z" fill="var(--blue)"/><circle cx="11" cy="9" r="2" fill="#fff"/></svg>
  <p class="contact-item" style="top:132px">4821 W. Juniper Mesa Rd., Ste. 12<br>Tucson, AZ 85742</p>
  <svg class="contact-icon" style="top:190px" width="22" height="22" viewBox="0 0 22 22"><circle cx="11" cy="11" r="11" fill="#fff"/><path d="M7 5l3 3-1.5 2c1 2 2 3 4 4l2-1.5 3 3-2 2C10 17 5 12 5 7z" fill="var(--blue)"/></svg>
  <p class="contact-item" style="top:192px">(520) 555-0148</p>
  <svg class="contact-icon" style="top:239px" width="22" height="22" viewBox="0 0 22 22"><circle cx="11" cy="11" r="11" fill="#fff"/><rect x="5" y="7" width="12" height="9" rx="1" fill="var(--blue)"/><path d="M5 8l6 4 6-4" fill="none" stroke="#fff" stroke-width="1.3"/></svg>
  <p class="contact-item" style="top:240px">info@quellbrookfillhouse.com</p>

  <div class="footer-rule"></div>
  <p class="copyright">Copyright 2026. Quellbrook Fill House . All rights reserved.</p>
</footer>

</body>
</html>
```